DJ Colm Vetter

I'm looking for a professional but still artsy/progressive design. I come from a hip hop/club DJ background playing a lot of underground music but have switched to doing more corporate parties and weddings recently. I am all about keeping the dancefloor moving and emotionally connecting with the crowd. I'd like a trendy/updated color palette. Something that's clean enough that looks professional but also trendy enough to convey that by the end of the night we'll be sweatily dancing to the latest hits. Some designers/artists I like: Tarn Olquist, Pavel Remy, Wendell Quarrie, Lumeno 7400, Silas Dravin.

```html
<!DOCTYPE html>
<html lang="en">
<head>
<meta charset="utf-8">
<title>DJ Colm Vetter — Business Card</title>
<link href="https://fonts.googleapis.com/css2?family=Noto+Serif:wght@400&display=swap" rel="stylesheet">
<style>
  :root {
    --page-bg: #3a2c1f;
    --card-bg: #0d0c1c;
    --card-edge: #15132a;
    --glow-violet: #7a4fd6;
    --glow-lilac: #d9c8ff;
    --glow-deep: #2a1a5c;
    --text-light: #f2f0fa;
    --rule: #8c87a8;
  }
  * { margin: 0; padding: 0; box-sizing: border-box; }
  html, body {
    width: 1200px;
    height: 1023px;
    overflow: hidden;
    background: var(--page-bg);
  }
  .stage {
    width: 1200px;
    height: 1023px;
    display: flex;
    align-items: center;
    justify-content: center;
  }
  .card {
    position: relative;
    width: 1000px;
    height: 571px;
    border-radius: 26px;
    overflow: hidden;
    background: var(--card-bg);
    box-shadow: 0 20px 50px rgba(0,0,0,0.45);
  }
  .card__photo {
    position: absolute;
    left: 0;
    top: 0;
    width: 100%;
    height: 410px;
    background:
      radial-gradient(ellipse 180px 150px at 78% 30%, var(--glow-lilac) 0%, rgba(217,200,255,0.55) 25%, rgba(122,79,214,0.5) 55%, transparent 100%),
      radial-gradient(ellipse 260px 210px at 48% 55%, rgba(160,120,240,0.75) 0%, rgba(90,55,190,0.55) 45%, transparent 100%),
      radial-gradient(ellipse 200px 170px at 18% 70%, rgba(122,79,214,0.55) 0%, transparent 100%),
      linear-gradient(180deg, var(--card-edge) 0%, var(--glow-deep) 55%, var(--card-bg) 100%);
    -webkit-mask-image: linear-gradient(180deg, #000 70%, transparent 100%);
            mask-image: linear-gradient(180deg, #000 70%, transparent 100%);
  }
  .card__info {
    position: absolute;
    left: 70px;
    right: 70px;
    bottom: 46px;
    display: flex;
    align-items: flex-end;
    font-family: "Noto Serif", Georgia, serif;
    color: var(--text-light);
  }
  .card__name {
    font-size: 38px;
    letter-spacing: 1px;
    text-transform: uppercase;
    line-height: 1;
    padding-right: 34px;
  }
  .card__rule {
    width: 1px;
    height: 118px;
    background: var(--rule);
    margin-right: 32px;
  }
  .card__contact {
    list-style: none;
    font-size: 26px;
    line-height: 1.3;
  }
</style>
</head>
<body>
  <main class="stage">
    <article class="card">
      <div class="card__photo" role="img" aria-label="Photo of two DJs performing at mixing decks under violet stage lights"></div>
      <div class="card__info">
        <h1 class="card__name">DJ Colm Vetter</h1>
        <span class="card__rule"></span>
        <ul class="card__contact">
          <li>+330 5817-3094</li>
          <li>info@DJColmVetter.com</li>
          <li>latesetsessions.com</li>
        </ul>
      </div>
    </article>
  </main>
</body>
</html>
```